Website Design for a Luxury Wedding & Events Company

We are launching a British luxury wedding & event planning consultancy business providing bespoke, elegant and first-class service to our discerning clients in the UK and abroad. We specialize in Weddings (which will have it's on page) however we also provide service for other occasion which will be included in a single page 'Events'.

We require a company website design befitting of our luxury brand. Once designed we will post another job to code the website so that it can be hosted by HostPlume.com.

The website has to set the tone for our business and type of premium service we provide. Our website design has to be BESPOKE and have a luxury and elegant look and feel about it.

PLEASE REFER TO THE IMAGES ATTACHED TO GET AN UNDERSTANDING OF THE DESIGN CONCEPT WE WANT. ALL DESIGNS SUBMITTED MUST FOLLOW THE CONCEPT SPECIFIED!!!

We appreciate that the current budget will not permit for the design of all pages referenced above, so we are happy to have designs for up to 3 pages initially; Landing page (we have attached an examples of what we want), 'Home' page (an example is also attached) and 'About' us page. When we are happy with a particular design we can add payment for remainder of the pages required.

The final website design will have the following pages:
1a) URL Landing Page (details below)
1b) Home
2) About
3) Luxury Weddings
4) Services (this can either be a separate tab or linked to 'Luxury Weddings' - however it does need to be a separate page)
subheadings are:
> Comprehensive Wedding Planning Service
> Wedding Day Coordination Service
> Consultancy Service
5) Events
6) Gallery
7) Testimonials
8) Contact

We have a concept of the website is as follows:
URL Landing Page:
Option 1: This should just be simple but makes an immediate statement.
We have attached an image of how this could potentially look. The logo featured in the photo example needs to be replaced with our logo (reference site: http://tesslovank.com/).

Option 2: Alternatively this could be an actually door in the middle of the page - Imagine the big black gloss door at Number 14 Corwell Terrace (London Prime Minister's home).

By clicking the door knocker on either options , the 'Home Page' will be opened.

Our tag line should also be tastefully integrated:
'Exclusive Events, Masterfully Produced, Distinctively Designed'

The 'HOME PAGE' - should look like a luxury boutique office or reception lounge (luxury table, luxury head chair and luxury 2 client chairs; elegant chandelier, beautiful flowers on the table, 2 flutes of champagne on the table; and filing cabinets with drawers that are labelled with different website pages, e.g. 'about us', 'services', 'gallery', etc. By clicking on the drawers the details behind that page will open up in a separate tab/page.)

Our tag line should be on the Home Page also.

The overall concept and look and feel of website is all about taking people on a journey and giving them a glimpse of the luxury service that awaits them.

Colours: We want the general look and feel of the website to be WHITE, or OFF-WHITE with soft hints of gold to match the logo (tab/page headings could be gold). The only dark page should be the URL Landing page (ref to website images attached).

The website and images need to be compatible with mobile devices, smartphones, Tabros, etc. In terms of fit to screen, resolution etc...

We require links to our Pagewall, Quillet, Snapvuely and Boardlyne Pages (links to be provided later)

This is the rough concept and looking for designers to try to elevate this vision. :-) We are open for designers to interpret this concept in their own way.

Website wording/content is all ready to go...

We have attached our logo, and some imagery to help...

Target Market(s)

Luxury Wedding & Events Market

Industry/Entity Type

Wedding Planner

Number of Pages Required

3 page

Font styles to use
Sans Serif

Colors
ffffff

Requirements
Must have
• Tag Line:
• 'Exquisite Events, Masterfully Produced, Distinctively Designed'

```html
<!DOCTYPE html>
<html lang="en">
<head>
<meta charset="utf-8">
<title>Elena Marlowe — Luxury Wedding &amp; Event Consultants</title>
<link href="https://fonts.googleapis.com/css2?family=Cinzel:wght@400;500&display=swap" rel="stylesheet">
<style>
  :root {
    --bg-deep: #1b140d;
    --bg-mid: #3a3126;
    --bg-light: #5a5146;
    --gold: #d9b873;
    --gold-light: #f3dfa8;
    --gold-dark: #a77e36;
    --button-top: #d2a95a;
    --button-bottom: #b0863c;
    --text-light: #f4efe6;
  }
  * { margin: 0; padding: 0; box-sizing: border-box; }
  html, body {
    width: 1200px;
    height: 745px;
    overflow: hidden;
    background: var(--bg-deep);
  }
  .landing {
    position: relative;
    width: 1200px;
    height: 745px;
    overflow: hidden;
    font-family: "Cinzel", serif;
  }
  .landing__photo {
    position: absolute;
    inset: 0;
    background:
      radial-gradient(ellipse 45% 60% at 62% 52%, rgba(110,100,88,0.55), transparent 70%),
      linear-gradient(125deg, #2a2016 0%, var(--bg-mid) 35%, var(--bg-light) 55%, #3d342a 75%, var(--bg-deep) 100%);
  }
  .brand {
    position: absolute;
    left: 0;
    top: 0;
    width: 1200px;
    text-align: center;
    color: var(--gold);
  }
  .brand__mark {
    position: absolute;
    left: 531px;
    top: 221px;
    width: 138px;
    height: 138px;
    border: 2px solid var(--gold);
    border-radius: 50%;
  }
  .brand__name {
    position: absolute;
    left: 0;
    top: 398px;
    width: 1200px;
    font-size: 52px;
    font-weight: 400;
    letter-spacing: 4px;
    line-height: 1;
  }
  .brand__tagline {
    position: absolute;
    left: 0;
    top: 457px;
    width: 1200px;
    font-size: 19px;
    font-weight: 400;
    letter-spacing: 2.4px;
    line-height: 1;
  }
  .enter-button {
    position: absolute;
    left: 525px;
    top: 507px;
    width: 151px;
    height: 46px;
    display: flex;
    align-items: center;
    justify-content: center;
    background: linear-gradient(var(--button-top), var(--button-bottom));
    border-radius: 2px;
    color: var(--text-light);
    font-size: 16px;
    letter-spacing: 1px;
    text-decoration: none;
    font-variant: small-caps;
  }
  .copyright {
    position: absolute;
    left: 0;
    top: 711px;
    width: 1200px;
    text-align: center;
    color: var(--text-light);
    font-size: 11px;
    letter-spacing: 0.4px;
    font-variant: small-caps;
  }
</style>
</head>
<body>
<main class="landing">
  <div class="landing__photo" role="img" aria-label="Softly blurred photograph of a cream wedding thank-you card with gold trim on a dark table"></div>

  <div class="brand">
    <span class="brand__mark" aria-hidden="true"></span>
    <h1 class="brand__name">ELENA MARLOWE</h1>
    <p class="brand__tagline">LUXURY WEDDING &amp; EVENT CONSULTANTS</p>
  </div>

  <a class="enter-button" href="#home">Enter here</a>

  <p class="copyright">Copyright © 2015 LedgerCrest.com. All rights reserved.</p>
</main>
</body>
</html>
```